THE LANTERN is a mystical scythian creature, which guarded a golden treasure.

i am a published author back in he 1970's...corvale, edgar fennick, pellam grove. my agent died and the companies have been bought.
i want to publish on my own and have 3 completed novels. DER FROST is the first. i need a book cover, spine and back cover design for the book.
i will use the book design as an important part of a website i am planning for this and the other 2 books. i will need a design for the other books once this is completed.

this book is a thriller; the second is a historical novel, the third is a comedy. i don't know, because of the differing contents whether there should be an consistency in the design. i think not.

i have an excellent Talvern review and will want phrases from it prominently on the design. i like to be involved in the process. although the thriller deals with the Nazis, i don't want a bunch of s.s. officers. I see the book as a labyrinth with almost unbearable twists and turns. it is not a person book, but driven by the PLOT.

the design must be setup for PrintNimbo ( zolvex ) for printing. Font is important.i like black, but not critical.

the Talvern review (below) has an excellent outline and telling of the book.

as the other 2 novels are completed and i need help with a website, this could be more than just one project.

Back Cover Details:
i would like a small photo and 2 line bio next to the photo.on back cover if it fits.... leaving room for the IBSN /barcode.
the cover, design and excerpts are critical for success and i am willing to work and pay extra to have it the best.
i have never done this before as my first 2 novels were published by traditional houses, so, you must forgive any awkwardness in the process.
thank you
+++++++

THIS IS THE TALVERN REVIEW OF THE BOOK::::::::::
DER FROST (THE LANTERN)
Waldbeck, Leonard
Manuscript
BOOK REVIEW
Waldbeck (A Winter of Surgeons, 1983, etc.) offers an animated chase through Boston and Europe as his characters unravel
a mystery involving six pairs of identical Jewish twins saved from a German concentration camp.
In 1965, Henri Castaud, a scientist fruitlessly searching for the secret of telepathy, receives a tantalizing report of
macabre experiments conducted by Otto Wendrich, a Nazi researcher on a similar mission. Castaud searches for the
twins who were the subjects of Wendrich’s experiments, and he gets help from Ilse Varga, the daughter of another
German who was a pawn in a scheme to smuggle unknown items of the collapsing Reich. The first twin they
discover—Greta Mosbach, a woman who had lived a solitary life in a Jewish neighborhood of Boston—is already dead,
the victim of a grisly murder. Her stomach had been sliced open and an odd, smaller tear made in the area of her
appendix. It soon turns out that, not long before her death, Mosbach discovered that she was a beneficiary of a mysterious
will. The search then jumps the Atlantic to England, where Corvin, the powerful company funding Castaud’s research,
pushes Delbury, the bank that served as an executor for the will, to release information on another set of twins—who also
turn out to be dead. The novel’s settings are vivid and refreshingly detailed and include a grotesque concentration camp
in Jena, Germany, as well as the Arcadian French Riviera. The cast of villains is equally colorful, and the story takes
many unexpected turns. Castaud, on the other hand, is a stock protagonist about whom readers learn little more than his
hair color, his profession, and the fact that he enjoys sailing. Corvin, meanwhile, has the convenient ability to coerce
any organization or suspect, but it’s never treated with any scrutiny itself. The novel could also have used a stronger
copy edit; for example, various characters’ thoughts are rendered inconsistently, either in all-caps or underlined. Despite
these issues, however, the overall story is excellent and a reason to look forward to more from this author.
An often audacious Nazi mystery with plenty of well-placed plot twists.

FOR ALL DESIGNERS!!!!!!!!!below is the story of DER FROST, ( THE LANTERN.)FOR THOSE DESIGNERS WHO COULD NOT OPEN THE FILE ON THE CONTEST PAGE.DER FROST (THE LANTERN)Waldbeck, RichardManuscriptBOOK REVIEWHirshhorn (A Winter of Surgeons, 1983, etc.) offers an animated chase through Boston and Europe as his characters unravela mystery involving six pairs of identical Jewish twins saved from a German concentration camp.In 1965, Henri Castaud, a scientist fruitlessly searching for the secret of telepathy, receives a tantalizing report ofmacabre experiments conducted by Otto Wendrich, a Nazi researcher on a similar mission. Castaud searches for thetwins who were the subjects of Wendrich’s experiments, and he gets help from Ilse Varga, the daughter of anotherGerman who was a pawn in a scheme to smuggle unknown items of the collapsing Reich. The first twin theydiscover—Greta Mosbach, a woman who had lived a solitary life in a Jewish neighborhood of Boston—is already dead,the victim of a grisly murder. Her stomach had been sliced open and an odd, smaller tear made in the area of herappendix. It soon turns out that, not long before her death, Mosbach discovered that she was a beneficiary of a mysteriouswill. The search then jumps the Atlantic to England, where Corvin, the powerful company funding Castaud’s research,pushes Delbury, the bank that served as an executor for the will, to release information on another set of twins—who alsoturn out to be dead. The novel’s settings are vivid and refreshingly detailed and include a grotesque concentration campin Jena, Germany, as well as the Arcadian French Riviera. The cast of villains is equally colorful, and the story takesmany unexpected turns. Castaud, on the other hand, is a stock protagonist about whom readers learn little more than hishair color, his profession, and the fact that he enjoys sailing. Corvin, meanwhile, has the convenient ability to coerceany organization or suspect, but it’s never treated with any scrutiny itself. The novel could also have used a strongercopy edit; for example, various characters’ thoughts are rendered inconsistently, either in all-caps or underlined. Despitethese issues, however, the overall story is excellent and a reason to look forward to more from this author.An often audacious Nazi mystery with plenty of well-placed plot twists. Added Tuesday, June 2, 2015

BUDGET NOW $700 !!!!!!! STORY DETAILS NOW UPLOADED TO THE BRIEF.

BUDGET OVER $700 !!!!!!!

adult; males; history buffs; world war II buffs; groups interested in mental telepathy;
people who want their money's worth ona challenging read; people who have faith in the Talvern Reviews.

Sans Serif
• arial.

• front and back cover, spine. a design which grabs enough to want to read back text.
• design to emphasize the puzzle, labyrinth,, riddle, complexity, deceptions, twists, false leads,masquerades,double-dealing, trickiness of the plot.
• presence of identical twins; a treasure.
• the naivety of the american; the duplicities of the germans; the diabolical schemes of the germans. the vulnerability of the children. the ??? suspect mental capability of the identical twins.
• marching nazis,
• ? prominent swastika.
• no horror.
• no supernatural mumbo-jumbo.

```html
<!DOCTYPE html>
<html lang="en">
<head>
<meta charset="utf-8">
<title>The Lantern — Cover and Spine</title>
<link rel="stylesheet" href="https://fonts.googleapis.com/css2?family=Bitter:wght@800&display=swap">
<style>
  :root {
    --backdrop: #7d9ea9;
    --cover: #e3e3e3;
    --spine: #dcdcdc;
    --ink: #111111;
    --maze-red: #d9401f;
    --maze-orange: #f09a24;
    --maze-yellow: #f3d21c;
    --cover-shadow: rgba(20, 40, 50, 0.28);
    --fold-line: rgba(0, 0, 0, 0.12);
  }
  html, body {
    margin: 0;
    padding: 0;
    overflow: hidden;
  }
  body {
    width: 1200px;
    height: 784px;
    background: var(--backdrop);
    display: flex;
    align-items: center;
    justify-content: center;
  }
  .book-wrap {
    display: flex;
    height: 680px;
    box-shadow: 0 10px 30px var(--cover-shadow);
  }
  .book-spine {
    position: relative;
    width: 66px;
    height: 100%;
    background: var(--spine);
    border-right: 1px solid var(--fold-line);
    display: flex;
    align-items: center;
    justify-content: center;
  }
  .spine-title {
    margin: 0;
    writing-mode: vertical-rl;
    font-family: "Bitter", Georgia, serif;
    font-weight: 800;
    font-size: 34px;
    letter-spacing: 0.5px;
    color: var(--ink);
    white-space: nowrap;
  }
  .book-cover {
    position: relative;
    width: 490px;
    height: 100%;
    background: var(--cover);
    overflow: hidden;
  }
  .book-title {
    margin: 0;
    position: absolute;
    top: 52px;
    left: 0;
    right: 0;
    text-align: center;
    font-family: "Bitter", Georgia, serif;
    font-weight: 800;
    font-size: 44px;
    letter-spacing: 0.5px;
    color: var(--ink);
  }
  .maze-medallion {
    position: absolute;
    left: 25px;
    top: 138px;
    width: 440px;
    height: 440px;
  }
</style>
</head>
<body>
  <div class="book-wrap">
    <aside class="book-spine">
      <p class="spine-title">The Lantern</p>
    </aside>

    <main class="book-cover">
      <h1 class="book-title">The Lantern</h1>

      <svg class="maze-medallion" viewBox="0 0 440 440" xmlns="http://www.w3.org/2000/svg"
           role="img" aria-label="Round labyrinth medallion of interlaced red, orange and yellow pathways around a central target">
        <defs>
          <radialGradient id="maze-tone" cx="50%" cy="50%" r="55%">
            <stop offset="0%" stop-color="#f3d21c"/>
            <stop offset="55%" stop-color="#f09a24"/>
            <stop offset="100%" stop-color="#d9401f"/>
          </radialGradient>
        </defs>
        <circle class="maze-field" cx="220" cy="220" r="220" fill="url(#maze-tone)"/>
      </svg>
    </main>
  </div>
</body>
</html>
```